Buch-/eBook-Cover für einen Elternratgeber
Zielgruppe
Buch: Elternratgeber
Titel: Werte lernen
Untertitel: Deinem Kind den richtigen Umgang beibringen
Wir sind der BRAM Verlag und suchen ein passendes Cover für unseren neuen Elternratgeber. Mit diesem Buch möchten wir Eltern unterstützen, ihren Kindern einen guten und verantwortungsvollen Umgang mit Geld zu vermitteln.
Anforderungen an das Cover-Design:
Bitte keinen Comicstil
Das Buch richtet sich an Eltern (nicht kindlich oder verspielt gestalten)
Keine direkte Darstellung von Geld (z. B. keine Münzen, Geldscheine, Sparschweine usw.)
Ob mit oder ohne Personen auf dem Cover: sind wir offen
Farbwahl und Bildsprache: gerne seriös, ansprechend und modern
Wir sind gespannt auf kreative und professionelle Vorschläge!
E-Book E-Book"
Das Design darf nicht zu überladen sein.

```html
<!DOCTYPE html>
<html lang="de">
<head>
<meta charset="utf-8">
<title>Werte lernen – Buchcover</title>
<link rel="stylesheet" href="https://fonts.googleapis.com/css2?family=Source+Serif+4:opsz,wght@8..60,700&family=Roboto:wght@500&display=swap">
<style>
  :root {
    --page-bg: #f6f6f4;
    --cover-green: #466b66;
    --cover-green-deep: #3d5f59;
    --cream: #f1dfc8;
    --ochre: #d29a4c;
    --ochre-light: #d9a24f;
  }
  html, body {
    margin: 0;
    width: 1200px;
    height: 1200px;
    overflow: hidden;
    background: var(--page-bg);
  }
  .cover {
    position: absolute;
    left: 207px;
    top: 51px;
    width: 785px;
    height: 1098px;
    background: linear-gradient(180deg, var(--cover-green) 0%, var(--cover-green-deep) 100%);
    overflow: hidden;
    box-shadow: 0 10px 30px rgba(0,0,0,0.12);
  }
  .cover-title {
    position: absolute;
    top: 20px;
    left: 0;
    width: 100%;
    margin: 0;
    text-align: center;
    font-family: "Source Serif 4", Georgia, serif;
    font-weight: 700;
    font-size: 142px;
    line-height: 114px;
    letter-spacing: -1px;
    color: var(--cream);
  }
  .cover-subtitle {
    position: absolute;
    top: 278px;
    left: 0;
    width: 100%;
    margin: 0;
    text-align: center;
    font-family: "Roboto", Arial, sans-serif;
    font-weight: 500;
    font-size: 29px;
    line-height: 40px;
    color: var(--cream);
  }
  .cover-illustration {
    position: absolute;
    left: 0;
    top: 0;
    width: 785px;
    height: 1098px;
  }
</style>
</head>
<body>
  <div class="cover">
    <svg class="cover-illustration" viewBox="0 0 785 1098" role="img" aria-label="Illustration: Mutter führt ihr Kind an der Hand einen sonnigen Hang hinauf">
      <circle cx="185" cy="460" r="90" fill="var(--ochre-light)"/>
      <polygon points="0,990 785,570 785,900 0,1098" fill="var(--ochre)"/>
    </svg>
    <h1 class="cover-title">Werte<br>lernen</h1>
    <p class="cover-subtitle">Deinem Kind den richtigen<br>Umgang beibringen</p>
  </div>
</body>
</html>
```